DESKHAVEN COSPACE Website design and coding

DESKHAVEN COSPACE

DESKHAVEN is Galveston’s first (and currently only) shared business co-working space. We share the same upscale, casual work environment, but we work independently on our own (or our team’s) projects and goals. For only a flat $195 membership fee per month, you have your very own all-inclusive, fun, personal business office environment. Website is written (Word file #12, below); and all pictures etc provided. Galveston is a beachy, coastal, historic city an hour from Houston, Texas USA. Logo (file 11 below) is temporary only.

Target Market(s)

Outside sales people, medical students looking for study hall, Houston companies looking for local office, real estate agents, graphic artists, entrepreneurs, etc

Contact Information for Business Card

will discuss --want to combine with current business card with multiple businesses

Logo Text

DESKHAVEN COSPACE

Coding

Coded - Design and coding required

Number of Pages Required

5+ page

Colors
ec1f27
fbed22

Requirements
Nice to have
• maroon/wine dominant with yellow and red accents, gray base are the colors of the space--website could coordinate--but open to creative ideas/combinations

```html
<!DOCTYPE html>
<html lang="en">
<head>
<meta charset="utf-8">
<title>Deskhaven Cospace</title>
<link href="https://fonts.googleapis.com/css2?family=Saira+Semi+Condensed:wght@500;600;700&family=Fira+Sans:wght@400;500;600&display=swap" rel="stylesheet">
<style>
:root{
  --green:#1f9e3e;
  --green-dark:#17822f;
  --blue:#1d4aa0;
  --navy:#1c2b4a;
  --ink:#222;
  --body:#444;
  --muted:#666;
  --light:#f3f3f3;
  --dark:#1b1b1b;
  --white:#fff;
}
*{margin:0;padding:0;box-sizing:border-box}
html,body{width:1200px;height:5051px;overflow:hidden}
body{font-family:"Fira Sans",sans-serif;color:var(--body);background:var(--white);position:relative}
.h{font-family:"Saira Semi Condensed",sans-serif}
.abs{position:absolute}
.btn{position:absolute;display:flex;align-items:center;justify-content:center;font-family:"Saira Semi Condensed",sans-serif;font-weight:700;font-size:14px;letter-spacing:.3px;text-transform:uppercase}
.btn-green{background:var(--green);color:var(--white);border-radius:3px}
.btn-outline{border:2px solid var(--white);color:var(--white);border-radius:2px}
.btn-line{border:2px solid var(--green);color:var(--green);border-radius:3px;font-size:12px}
.rule{position:absolute;height:3px;width:84px;background:#555;left:50%;margin-left:-42px}

/* header */
.site-header{position:absolute;top:0;left:0;width:1200px;height:88px;background:var(--white)}
.brand{position:absolute;left:40px;top:22px;display:flex;align-items:center;gap:12px}
.brand-dot{width:44px;height:44px;border-radius:50%;background:var(--blue)}
.brand-name{font-family:"Saira Semi Condensed",sans-serif;font-weight:700;font-size:20px;line-height:22px;color:var(--blue);width:170px}
.main-nav{position:absolute;left:362px;top:35px;display:flex;gap:20px;font-family:"Saira Semi Condensed",sans-serif;font-weight:600;font-size:13px;color:var(--navy);text-transform:uppercase}
.main-nav .active{color:var(--blue)}
.quote{left:975px;top:22px;width:193px;height:46px;box-shadow:0 3px 6px rgba(0,0,0,.2)}

/* hero */
.hero{position:absolute;top:88px;left:0;width:1200px;height:677px;background:linear-gradient(90deg,#7a1a2a 0%,#3a2e2a 30%,#4a443c 55%,#d8d0bd 80%,#5b1b27 100%)}
.hero-shade{position:absolute;inset:0;background:linear-gradient(180deg,rgba(0,0,0,.15),rgba(0,0,0,.35))}
.hero-title{position:absolute;top:200px;width:1200px;text-align:center;color:var(--white);font-family:"Saira Semi Condensed",sans-serif;font-weight:600;font-size:38px;line-height:47px;text-transform:uppercase;text-shadow:0 2px 6px rgba(0,0,0,.4)}
.hero .btn{left:514px;top:322px;width:172px;height:45px}
.hero-arrows{position:absolute;left:562px;top:624px}

/* about */
.about-title{position:absolute;top:820px;width:1200px;text-align:center;font-weight:700;font-size:33px;color:var(--ink)}
.about-title span{color:var(--green)}
.about-text{position:absolute;top:905px;left:140px;width:920px;text-align:center;font-size:14.5px;line-height:25px;color:var(--body)}

/* feature tiles */
.tile{position:absolute;top:1052px;width:394px;height:500px}
.tile-photo{position:absolute;inset:0}
.tile-bar-top{position:absolute;top:-7px;left:0;width:160px;height:7px;background:var(--green)}
.tile-bar-bottom{position:absolute;bottom:-7px;right:0;width:160px;height:7px;background:var(--green)}
.tile-title{position:absolute;top:187px;width:100%;text-align:center;color:var(--white);font-family:"Saira Semi Condensed",sans-serif;font-weight:600;font-size:21px;line-height:31px;text-transform:uppercase;text-shadow:0 2px 5px rgba(0,0,0,.5)}
.tile .btn{left:113px;top:266px;width:168px;height:46px;font-size:13px}

/* membership */
.membership{position:absolute;top:1632px;left:0;width:1200px;height:676px;background:var(--light)}
.member-photo{position:absolute;left:0;top:0;width:632px;height:676px;background:linear-gradient(135deg,#6d6a63,#3b3833 45%,#8f8a80 80%,#2e2b27)}
.member-title{position:absolute;left:697px;top:56px;font-weight:700;font-size:31px;color:var(--ink)}
.member-rule{position:absolute;left:697px;top:107px;width:76px;height:3px;background:#555}
.member-box{position:absolute;left:632px;width:480px;height:116px;background:var(--white);box-shadow:0 2px 8px rgba(0,0,0,.12)}
.member-box p{position:absolute;left:65px;right:20px;top:50%;transform:translateY(-50%);font-size:14px;line-height:21px;color:var(--body)}
.member-icon{position:absolute;left:-62px;top:50%;margin-top:-50px;width:100px;height:100px;border-radius:50%;background:var(--white);box-shadow:0 2px 8px rgba(0,0,0,.2);display:flex;align-items:center;justify-content:center}
.member-icon svg{width:84px;height:84px}
.membership .btn{left:948px;top:575px;width:164px;height:45px}

/* philosophy */
.philo-title{position:absolute;top:2388px;width:1200px;text-align:center;font-weight:700;font-size:35px;color:var(--ink)}
.card{position:absolute;top:2497px;width:289px;height:468px;background:var(--white);border:1px solid #ddd;box-shadow:0 2px 6px rgba(0,0,0,.08)}
.card-photo{height:207px;width:100%}
.card h3{font-family:"Fira Sans",sans-serif;font-weight:600;font-size:13.5px;line-height:20px;color:var(--ink);margin:30px 22px 0;text-transform:uppercase}
.card p{font-size:13px;line-height:21.5px;color:var(--body);margin:8px 22px 0;height:108px;overflow:hidden}
.card .btn{left:22px;bottom:32px;width:140px;height:38px}

/* amenities */
.amenities{position:absolute;top:3060px;left:0;width:1200px;height:778px;background:linear-gradient(180deg,#262626,#1e1e1e 60%,#2a2a2a)}
.amen-title{position:absolute;top:76px;width:1200px;text-align:center;color:var(--white);font-weight:700;font-size:37px}
.amen-intro{position:absolute;top:150px;left:230px;width:740px;text-align:center;color:#ddd;font-size:14.5px;line-height:24px}
.amen{position:absolute;width:170px;text-align:center;color:#ddd;font-size:14px;line-height:20px}
.amen-icon{width:110px;height:110px;margin:0 auto 12px;border-radius:50%;background:var(--green);border:3px solid var(--white);display:flex;align-items:center;justify-content:center}
.amen-icon svg{width:64px;height:64px}

/* testimonials */
.client-title{position:absolute;top:3912px;width:1200px;text-align:center;font-weight:700;font-size:31px;color:#333}
.quote-card{position:absolute;left:267px;top:4027px;width:666px;height:232px;background:var(--white);box-shadow:0 4px 18px rgba(0,0,0,.12)}
.quote-card p{position:absolute;left:90px;right:90px;top:40px;text-align:center;font-size:15px;line-height:27px;color:var(--body)}
.quote-mark{position:absolute;font-family:Georgia,serif;font-weight:700;font-size:52px;color:var(--ink);line-height:1}
.quote-name{position:absolute;top:154px;width:100%;text-align:center;font-size:14px;color:var(--body);text-transform:uppercase}
.avatar{position:absolute;left:543px;top:4234px;width:114px;height:114px;border-radius:50%;background:linear-gradient(135deg,#6b7e8c,#2d3a44);border:4px solid var(--white)}
.client-halo{position:absolute;top:3990px;width:260px;height:300px;border-radius:130px 130px 20px 20px;background:radial-gradient(circle at 50% 35%,rgba(31,158,62,.08),rgba(200,210,230,.18) 60%,transparent 75%)}

/* contact */
.contact{position:absolute;top:4398px;left:0;width:1200px;height:522px;background:var(--dark)}
.contact-title{position:absolute;top:110px;width:1200px;text-align:center;color:var(--white);font-weight:700;font-size:34px}
.info{position:absolute;left:145px;display:flex;gap:16px;color:var(--white);font-size:14px;line-height:19px;font-weight:500}
.info-icon{width:44px;height:44px;border-radius:50%;background:var(--white);flex:none;display:flex;align-items:center;justify-content:center}
.field{position:absolute;background:var(--white);height:40px;font-size:12px;color:#555;padding:13px 16px}
.contact .btn{left:540px;top:412px;width:153px;height:42px}

.site-footer{position:absolute;top:4920px;left:0;width:1200px;height:131px;background:var(--dark);border-top:1px solid #333;text-align:center;color:#ddd;font-size:13px;padding-top:60px}
</style>
</head>
<body>

<header class="site-header">
  <div class="brand"><span class="brand-dot"></span><span class="brand-name">DESKHAVEN COSPACE</span></div>
  <nav class="main-nav">
    <span class="active">Home</span><span>About</span><span>Amenities</span><span>Membership</span><span>Pictures</span><span>The Deskhaven Philosophy</span><span>Contact</span>
  </nav>
  <div class="btn btn-green quote">Request a Quote</div>
</header>

<section class="hero" role="img" aria-label="Lounge with red lockers and leather sofas">
  <div class="hero-shade"></div>
  <h1 class="hero-title">Deskhaven Cospace<br>Shared Business Co-working Space</h1>
  <div class="btn btn-green">Find Out More</div>
  <svg class="hero-arrows" width="76" height="20" viewBox="0 0 76 20">
    <path d="M32 10H4M12 3 4 10l8 7" stroke="#fff" stroke-width="3" fill="none"/>
    <path d="M44 10h28M64 3l8 7-8 7" stroke="#1f9e3e" stroke-width="3" fill="none"/>
  </svg>
</section>

<h2 class="about-title h"><span>ABOUT</span> DESKHAVEN COSPACE</h2>
<div class="rule" style="top:883px"></div>
<p class="about-text">DESKHAVEN is Galveston’s first (and currently only) shared business co-working space.&nbsp; We share the same upscale, casual work environment, but we work independently on our own (or our team’s) projects and goals.&nbsp; For only a flat $195 membership fee per month, you have your very own all-inclusive, fun, personal business office environment.</p>

<div class="tile" style="left:0">
  <div class="tile-photo" role="img" aria-label="Open co-working area with pendant lights" style="background:linear-gradient(160deg,#8a8560,#3e3a2c 55%,#2a2a26)"></div>
  <div class="tile-bar-top"></div><div class="tile-bar-bottom"></div>
  <div class="tile-title">Shared Business<br>Co-working Space</div>
  <div class="btn btn-outline">Learn More</div>
</div>
<div class="tile" style="left:400px">
  <div class="tile-photo" role="img" aria-label="Private cubicles with desk chairs" style="background:linear-gradient(160deg,#6f7880,#3a3f44 55%,#26292b)"></div>
  <div class="tile-bar-top"></div><div class="tile-bar-bottom"></div>
  <div class="tile-title">Casual Work<br>Environment</div>
  <div class="btn btn-outline">Learn More</div>
</div>
<div class="tile" style="left:800px">
  <div class="tile-photo" role="img" aria-label="Coffee bar with stools and hanging lamps" style="background:linear-gradient(160deg,#b9b27a,#5a2a2e 55%,#2b2422)"></div>
  <div class="tile-bar-top"></div><div class="tile-bar-bottom"></div>
  <div class="tile-title">We Share<br>The Same Upscale</div>
  <div class="btn btn-outline">Learn More</div>
</div>

<section class="membership">
  <div class="member-photo" role="img" aria-label="Shared kitchen with steel fridge and stools"></div>
  <h2 class="member-title h">MEMBERSHIP</h2>
  <div class="member-rule"></div>
  <div class="member-box" style="top:143px;left:697px;width:415px">
    <div class="member-icon"><svg viewBox="0 0 84 84"><circle cx="42" cy="42" r="40" fill="#1d4aa0"/><rect x="24" y="26" width="36" height="32" rx="3" fill="none" stroke="#fff" stroke-width="2.5"/><path d="M24 35h36M32 22v8M52 22v8" stroke="#fff" stroke-width="2.5"/><circle cx="54" cy="54" r="8" fill="#1d4aa0" stroke="#fff" stroke-width="2.5"/></svg></div>
    <p>For only $195 a month, charged to your credit card, you get the all-inclusive amenities listed above, for one flat fee.&nbsp; The only “extras” are for copies, on a per-copy basis.</p>
  </div>
  <div class="member-box" style="top:287px;left:697px;width:415px">
    <div class="member-icon"><svg viewBox="0 0 84 84"><circle cx="42" cy="42" r="40" fill="#1d4aa0"/><path d="M24 36a26 26 0 0 1 36 0M29 42a18 18 0 0 1 26 0M34 48a10 10 0 0 1 16 0" fill="none" stroke="#fff" stroke-width="2.5"/><rect x="28" y="54" width="28" height="8" rx="2" fill="none" stroke="#fff" stroke-width="2.5"/></svg></div>
    <p>WiFi, coffee, use of the conference room, office use, use of the kitchen and all the other features listed under “AMENITIES” above, are INCLUDED at no additional cost.</p>
  </div>
  <div class="member-box" style="top:431px;left:697px;width:415px">
    <div class="member-icon"><svg viewBox="0 0 84 84"><circle cx="42" cy="42" r="40" fill="#1d4aa0"/><circle cx="36" cy="32" r="7" fill="none" stroke="#fff" stroke-width="2.5"/><path d="M22 58c0-9 6-14 14-14s14 5 14 14z" fill="none" stroke="#fff" stroke-width="2.5"/><rect x="46" y="44" width="16" height="14" fill="none" stroke="#fff" stroke-width="2.5"/></svg></div>
    <p>Get a FREE day, to try us out by emailing us at the link here</p>
  </div>
  <div class="btn btn-green">Learn More</div>
</section>

<h2 class="philo-title h">THE DESKHAVEN PHILOSOPHY</h2>
<div class="rule" style="top:2451px"></div>

<article class="card" style="left:143px">
  <div class="card-photo" role="img" aria-label="Office corner with printer" style="background:linear-gradient(135deg,#8b8a86,#d4d2c9 50%,#6c6a64)"></div>
  <h3>Work outside the home</h3>
  <p>Free yourself for the burdens of house or school, and work in an environment that MOTIVATES you instead of DISTRACTS you.&nbsp; Meet like-minded people that can help you along, and</p>
  <div class="btn btn-line">Read More</div>
</article>
<article class="card" style="left:456px">
  <div class="card-photo" role="img" aria-label="Cubicle row with gaming chairs" style="background:linear-gradient(135deg,#5d6470,#a7a49a 50%,#3c3f45)"></div>
  <h3>Deskhaven the competition</h3>
  <p>Because of the flexibility, prestigious location, opportunities to meet and network with active professionals, and the available tech and amenities, you have all the tools you need to</p>
  <div class="btn btn-line">Read More</div>
</article>
<article class="card" style="left:768px">
  <div class="card-photo" role="img" aria-label="Coffee bar and kitchen counter" style="background:linear-gradient(135deg,#c8c29a,#5b2a30 55%,#2d2624)"></div>
  <h3>Work it out with your coworkers</h3>
  <p>DESKHAVEN is a community – if you are making a pot of (free) coffee – ask and make enough for everyone that wants some!&nbsp; You rapidly become</p>
  <div class="btn btn-line">Read More</div>
</article>

<section class="amenities">
  <h2 class="amen-title h">AMENITIES</h2>
  <div class="rule" style="top:130px;background:#fff"></div>
  <p class="amen-intro">DESKHAVEN is the first Galveston co-working space, and offers all of the following features, all included in your monthly $195 membership fee:</p>

  <div class="amen" style="left:122px;top:258px"><div class="amen-icon"><svg viewBox="0 0 64 64" fill="none" stroke="#fff" stroke-width="2.5"><rect x="20" y="10" width="24" height="44"/><path d="M26 18h4M34 18h4M26 26h4M34 26h4M26 34h4M34 34h4M28 54v-10h8v10M8 54h48"/></svg></div>Open office or a private cubicle for your daily use</div>
  <div class="amen" style="left:317px;top:258px"><div class="amen-icon"><svg viewBox="0 0 64 64" fill="none" stroke="#fff" stroke-width="2.5"><path d="M10 26a31 31 0 0 1 44 0M17 33a21 21 0 0 1 30 0M24 40a11 11 0 0 1 16 0"/><rect x="16" y="46" width="32" height="8" rx="2"/></svg></div>Free Wifi</div>
  <div class="amen" style="left:513px;top:258px"><div class="amen-icon"><svg viewBox="0 0 64 64" fill="none" stroke="#fff" stroke-width="2.5"><circle cx="26" cy="24" r="14"/><path d="M26 16v8l6 4M36 44h20v10H36zM8 54h24"/></svg></div>24 hour access</div>
  <div class="amen" style="left:709px;top:258px"><div class="amen-icon"><svg viewBox="0 0 64 64" fill="none" stroke="#fff" stroke-width="2.5"><rect x="22" y="10" width="26" height="18"/><path d="M35 28v6M10 38h44M14 38v16M50 38v16M20 44h10"/></svg></div>Comfortable open casual spaces or private office</div>
  <div class="amen" style="left:905px;top:258px"><div class="amen-icon"><svg viewBox="0 0 64 64" fill="none" stroke="#fff" stroke-width="2.5"><rect x="10" y="30" width="44" height="24"/><path d="M10 40h44M32 30v24M20 14h10v10H20zM40 12v16"/></svg></div>Communal coffee bar and kitchen, with FREE coffee</div>

  <div class="amen" style="left:122px;top:482px"><div class="amen-icon"><svg viewBox="0 0 64 64" fill="none" stroke="#fff" stroke-width="2.5"><rect x="16" y="12" width="30" height="42" rx="2"/><path d="M26 8h10v8H26zM31 26v12M25 32h12M22 46h18"/></svg></div>Health and social distance amenities, including hand</div>
  <div class="amen" style="left:317px;top:482px"><div class="amen-icon"><svg viewBox="0 0 64 64" fill="none" stroke="#fff" stroke-width="2.5"><circle cx="32" cy="16" r="6"/><circle cx="16" cy="36" r="6"/><circle cx="48" cy="36" r="6"/><path d="M24 30c0-5 4-7 8-7s8 2 8 7M6 54c0-6 4-9 10-9s10 3 10 9M38 54c0-6 4-9 10-9s10 3 10 9"/></svg></div>Great opportunity for networking or mentoring</div>
  <div class="amen" style="left:513px;top:482px"><div class="amen-icon"><svg viewBox="0 0 64 64" fill="none" stroke="#fff" stroke-width="2.5"><circle cx="18" cy="20" r="5"/><circle cx="32" cy="18" r="5"/><circle cx="46" cy="20" r="5"/><path d="M8 36h48M14 36v18M50 36v18M12 32c0-5 3-7 6-7s6 2 6 7M40 32c0-5 3-7 6-7s6 2 6 7"/></svg></div>Private conference rooms for meetings</div>
  <div class="amen" style="left:709px;top:482px"><div class="amen-icon"><svg viewBox="0 0 64 64" fill="none" stroke="#fff" stroke-width="2.5"><rect x="14" y="10" width="36" height="22"/><path d="M20 26l8-8 6 5 10-9M10 42h44M16 42v12M48 42v12"/></svg></div>Free conference presentation room, on a shared, scheduled basis.</div>
  <div class="amen" style="left:905px;top:482px"><div class="amen-icon"><svg viewBox="0 0 64 64" fill="none" stroke="#fff" stroke-width="2.5"><rect x="12" y="10" width="40" height="44"/><path d="M32 10v44M24 28v6M40 28v6"/></svg></div>Private lockable lockers</div>
</section>

<h2 class="client-title h">OUR CLIENT SAY</h2>
<div class="rule" style="top:3965px;width:70px;margin-left:-35px"></div>
<div class="client-halo" style="left:120px"></div>
<div class="client-halo" style="left:820px"></div>
<svg class="abs" style="left:182px;top:4120px" width="24" height="36" viewBox="0 0 24 36"><path d="M20 4 6 18l14 14" stroke="#777" stroke-width="3" fill="none"/></svg>
<svg class="abs" style="left:994px;top:4120px" width="24" height="36" viewBox="0 0 24 36"><path d="M4 4l14 14L4 32" stroke="#777" stroke-width="3" fill="none"/></svg>
<div class="quote-card">
  <span class="quote-mark" style="left:88px;top:30px">“</span>
  <p>&nbsp;&nbsp;&nbsp;&nbsp;&nbsp;&nbsp;Nemo enim ipsam voluptatem quia voluptas sit aspernatur aut odit aut fugit, sed quia consequuntur magni dolores eos qui ratione voluptatem sequi nesciunt. Neque porro quisquam est, qui dolorem ipsum quia dolor sit amet, consectetur</p>
  <div class="quote-name">Deskhaven Cospace</div>
  <span class="quote-mark" style="left:500px;top:150px">”</span>
</div>
<div class="avatar" role="img" aria-label="Client photo"></div>

<section class="contact">
  <svg class="abs" style="left:0;top:-30px" width="1200" height="40" viewBox="0 0 1200 40" preserveAspectRatio="none"><path d="M0 40 600 0l600 40z" fill="#1f9e3e"/><path d="M0 40 600 8l600 32z" fill="#1b1b1b"/></svg>
  <h2 class="contact-title h">CONTACT US</h2>
  <div class="info" style="top:196px"><span class="info-icon"><svg width="20" height="22" viewBox="0 0 20 22"><path d="M10 1a7 7 0 0 0-7 7c0 5 7 13 7 13s7-8 7-13a7 7 0 0 0-7-7z" fill="#1f9e3e"/><circle cx="10" cy="8" r="2.5" fill="#fff"/></svg></span><div>Deskhaven Cospace<br>652 enim ipsam voluptatem<br>quia voluptas sit</div></div>
  <div class="info" style="top:278px"><span class="info-icon"><svg width="20" height="20" viewBox="0 0 20 20"><path d="M4 1l4 4-2 3c1 2 3 4 5 5l3-2 4 4-3 3C8 18 2 12 1 4z" fill="#1f9e3e"/></svg></span><div>Phone<br>+808 2002 46169</div></div>
  <div class="info" style="top:360px"><span class="info-icon"><svg width="22" height="16" viewBox="0 0 22 16"><rect x="1" y="1" width="20" height="14" rx="2" fill="#1f9e3e"/><path d="M2 2l9 7 9-7" stroke="#fff" stroke-width="1.6" fill="none"/></svg></span><div>Email<br>info@deskhavencospace.com</div></div>

  <div class="field" style="left:540px;top:198px;width:252px">First name</div>
  <div class="field" style="left:804px;top:198px;width:252px">Last Name</div>
  <div class="field" style="left:540px;top:247px;width:252px">Email</div>
  <div class="field" style="left:804px;top:247px;width:252px">Phone Number</div>
  <div class="field" style="left:540px;top:296px;width:516px;height:98px">Message</div>
  <div class="btn btn-green">Submit</div>
</section>

<footer class="site-footer">(c) 2020 Deskhaven Cospace&nbsp; | All Rights Reserved</footer>

</body>
</html>
```